Square graphic for social media post

I want to create a 1080 x 1080px all-black image for the quote below that I can share on social media. I want the emphasis to be primarily on the quote, secondarily on the portrait, and third (smallest) on the logo. I want the background on the portrait to be edited so it's transparent and just shows the face of the person on a black background (no brick wall visible).

Graphic color: black
Text color: white
Content: "What we went through is going to make the greatest generation of hoteliers our industry has ever seen." << biggest text
Derek Holm << smaller text
President, Silverbrook Hotels << smaller text
[image of person - use whichever version looks better to you]
[Add Lodging Ledger logo - whichever looks better to you]

This image needs to be readable when sized down much smaller (400x400?) so want the text and portrait to take up most of the space.

I'd like the output both as PNG and original file (preferably Canva). Thanks!

Target Market(s)

Hotel managers

Industry/Entity Type

Hospitality

Font styles to use
Sans Serif

Colors

Designer to choose colors to be used in the design.

Requirements
Must have
• Needs to focus on the quote and the person quoted (the portrait)

```html
<!DOCTYPE html>
<html lang="en">
<head>
<meta charset="utf-8">
<title>Quote Card – Derek Holm</title>
<link rel="stylesheet" href="https://fonts.googleapis.com/css2?family=Barlow+Semi+Condensed:wght@800&family=Oswald:wght@600&family=Open+Sans:wght@600;700&display=swap">
<style>
  :root {
    --bg: #000000;
    --ink: #ffffff;
    --portrait-light: #b9b9b9;
    --portrait-dark: #3a3a3a;
  }
  html, body {
    margin: 0;
    padding: 0;
    width: 1200px;
    height: 1200px;
    overflow: hidden;
    background: var(--bg);
  }
  .card {
    position: relative;
    width: 1200px;
    height: 1200px;
    background: var(--bg);
    color: var(--ink);
    overflow: hidden;
  }
  .quote-mark {
    position: absolute;
    font-family: "Barlow Semi Condensed", sans-serif;
    font-weight: 800;
    font-size: 90px;
    line-height: 1;
    color: var(--ink);
  }
  .quote-mark--open { left: 118px; top: 68px; }
  .quote-mark--close { left: 830px; top: 862px; }
  .quote-text {
    position: absolute;
    left: 120px;
    top: 156px;
    margin: 0;
    font-family: "Barlow Semi Condensed", sans-serif;
    font-weight: 800;
    font-size: 96px;
    line-height: 90px;
    text-transform: uppercase;
    letter-spacing: 0;
    white-space: nowrap;
  }
  .brand-mark {
    position: absolute;
    left: 960px;
    top: 330px;
    width: 480px;
    height: 480px;
    border-radius: 50%;
    background: var(--ink);
  }
  .brand-name {
    position: absolute;
    right: 60px;
    top: 850px;
    font-family: "Barlow Semi Condensed", sans-serif;
    font-weight: 800;
    font-size: 30px;
    text-transform: uppercase;
    color: var(--ink);
  }
  .attribution {
    position: absolute;
    left: 139px;
    top: 942px;
    display: flex;
    align-items: center;
  }
  .portrait {
    width: 159px;
    height: 156px;
    border: 5px solid var(--ink);
    background: radial-gradient(circle at 50% 40%, var(--portrait-light), var(--portrait-dark));
  }
  .speaker-name {
    margin-left: 36px;
    font-family: "Oswald", sans-serif;
    font-weight: 600;
    font-size: 50px;
    letter-spacing: -1px;
  }
  .speaker-role {
    margin-left: 30px;
    margin-top: -10px;
    font-family: "Open Sans", sans-serif;
    text-transform: uppercase;
    line-height: 1.15;
  }
  .speaker-role__title { font-weight: 700; font-size: 20px; }
  .speaker-role__company { font-weight: 600; font-size: 16px; }
</style>
</head>
<body>
  <main class="card">
    <span class="quote-mark quote-mark--open" aria-hidden="true">&ldquo;</span>
    <blockquote class="quote-text">
      What we went<br>
      through is going<br>
      to make the<br>
      greatest<br>
      generation<br>
      of hoteliers<br>
      our industry<br>
      has ever seen
    </blockquote>
    <span class="quote-mark quote-mark--close" aria-hidden="true">&rdquo;</span>

    <div class="brand-mark" aria-hidden="true"></div>
    <div class="brand-name">Lodging Ledger</div>

    <div class="attribution">
      <div class="portrait" role="img" aria-label="Black and white headshot portrait of Derek Holm"></div>
      <div class="speaker-name">Derek Holm</div>
      <div class="speaker-role">
        <div class="speaker-role__title">President</div>
        <div class="speaker-role__company">Silverbrook Hotels</div>
      </div>
    </div>
  </main>
</body>
</html>
```